Tiroler party ecommerce site

We have a eCommerce site that needs a redesign. What we need are 3 pages: a frontpage, a product listing page and a product page.

The look has to be:
fun, modern, fresh, bright, professional look but not corporate.

Some content keywords are :
Carnival, oktoberfesten, tirol, dirndl, leder hosen, beer, women with big breast (no porn! just fun)

Some functional hints :

The frontpage needs to give a good impression of all the products on the site.
There should also be some space for campaigns or banners on the frontpage.

The product listing page should have facets (search options) and a search field.

The product page should have a few boxes such as related products, others viewed, comments etc.. (your average product page content)

All pages should show a small cart button or box and off course a kick ass menu!

Some links :

The current site http://www.feestkraamwinkel.nl/

We couldn't find any site to show as inspiration most party sites are very bad!.

```html
<!DOCTYPE html>
<html lang="en">
<head>
<meta charset="utf-8">
<title>Feestkraamwinkel – Clothing Accessories</title>
<link href="https://fonts.googleapis.com/css2?family=Arimo:wght@400;700&display=swap" rel="stylesheet">
<style>
:root{
  --green:#67ab00;
  --green-dark:#5a9900;
  --ink:#2b2b2b;
  --text:#555;
  --muted:#888;
  --line:#e2e2e2;
  --panel:#f3f3f3;
  --topbar:#ececec;
  --red:#e3241b;
  --white:#fff;
}
*{box-sizing:border-box;margin:0;padding:0}
html,body{width:1200px;height:1093px;overflow:hidden;background:var(--white)}
body{font-family:"Arimo",Arial,sans-serif;color:var(--text);font-size:9px}
.canvas{position:relative;width:1200px;height:1093px;overflow:hidden}
.abs{position:absolute}

/* backgrounds */
.topbar{left:0;top:0;width:1200px;height:22px;background:var(--topbar)}
.backdrop{left:0;top:161px;width:1200px;height:853px;
  background:linear-gradient(90deg,#5d6a55 0%,#8a9b7d 8%,#c9cfb8 16%,#7f8d78 20%,#4d5a4c 40%,#6f7d72 60%,#9ab0b6 80%,#d4dac8 90%,#b8c6b5 100%)}
.ground{left:0;top:1014px;width:1200px;height:79px;background:var(--green)}
.shell{left:237px;top:111px;width:743px;height:958px;background:var(--panel)}

/* top bar */
.welcome{left:237px;top:7px;font-size:7px;color:var(--muted);letter-spacing:.1px}
.welcome b{color:var(--ink)}
.welcome em{font-style:normal;color:var(--green);font-weight:700}
.currency{top:0;height:22px;width:47px;background:#dcdcdc;color:#999;font-size:7.5px;line-height:22px;text-align:center}
.account-links{right:220px;top:7px;font-size:7.5px;color:var(--ink)}
.account-links span{color:#999;margin:0 6px}

/* header */
.brand{left:237px;top:74px;width:175px;display:flex;align-items:center;gap:6px;color:var(--green);font-size:17px;font-weight:700;white-space:nowrap}
.brand i{display:block;flex:none;width:10px;height:10px;border-radius:50%;background:var(--green)}
.search{left:424px;top:71px;width:386px;height:25px;border:1px solid #d6d6d6;background:var(--white)}
.search .cat{position:absolute;left:0;top:0;width:104px;height:23px;border-right:1px solid #d6d6d6;font-size:7.5px;color:var(--muted);padding:8px 0 0 20px}
.search .cat:after{content:"";position:absolute;right:8px;top:10px;border:3px solid transparent;border-top-color:#aaa}
.search .field{position:absolute;left:118px;top:8px;font-size:7.5px;color:#aaa}
.search .go{position:absolute;right:-1px;top:-1px;width:25px;height:25px;background:var(--green)}
.mini-cart{left:831px;top:71px;width:149px;height:26px;border:1px solid #cfcfcf;background:#f4f4f4;font-size:9px;color:var(--ink)}
.mini-cart .count{position:absolute;left:42px;top:8px}
.mini-cart .drop{position:absolute;right:0;top:0;width:26px;height:24px;border-left:1px solid #cfcfcf}
.mini-cart .drop:after{content:"";position:absolute;left:9px;top:10px;border:4px solid transparent;border-top-color:#333}

/* navigation */
.nav-products{left:258px;top:131px;width:147px;height:30px;background:var(--ink);color:var(--white);font-weight:700;font-size:8.5px;padding:10px 0 0 15px}
.nav-products:after{content:"";position:absolute;right:16px;top:10px;width:5px;height:5px;border-right:1.5px solid #aaa;border-bottom:1.5px solid #aaa;transform:rotate(45deg)}
.nav-main{left:405px;top:131px;width:457px;height:30px;background:var(--green);display:flex;color:var(--white);font-size:8.5px}
.nav-main a{display:block;padding:10px 0 0;text-decoration:none;color:var(--white)}
.nav-cart{left:862px;top:131px;width:100px;height:30px;background:var(--ink);color:var(--white);font-size:8.5px;font-weight:700;padding:10px 0 0 34px}

/* main */
.content{left:410px;top:161px;width:552px;height:648px;background:var(--white)}
.side-box{background:var(--white);border:1px solid #e4e4e4}
.cat-list{left:258px;top:164px;width:148px;height:213px}
.cat-item{position:absolute;left:15px;width:117px;font-size:8px;color:var(--text);padding-bottom:5px;border-bottom:1px dashed #c8c8c8}
.cat-item.active{color:var(--green)}
.cat-item.last{border-bottom:0}
.flyout{left:405px;top:166px;width:189px;height:211px;background:var(--green);color:var(--white)}
.flyout:before{content:"";position:absolute;left:-6px;top:132px;border:6px solid transparent;border-left:0;border-right-color:var(--green)}
.flyout h3{position:absolute;left:19px;top:25px;font-weight:400;font-size:14px}
.flyout .rule{position:absolute;left:19px;top:47px;width:132px;height:1px;background:rgba(255,255,255,.55)}
.flyout a{position:absolute;left:19px;font-size:8.5px;color:var(--white);text-decoration:none}
.flyout a.current{color:var(--ink)}
.top-rule{left:594px;top:213px;width:339px;height:1px;background:var(--line)}

.card{width:157px;height:145px;background:var(--white);border:1px solid #e6e6e6;text-align:center}
.card.featured{border-color:var(--green)}
.card .pic{position:absolute;left:44px;top:28px;width:68px;height:38px;border-radius:14px}
.pic.bavarian{background:linear-gradient(135deg,#9fc2e6,#d8c6a0)}
.pic.green-glasses{background:linear-gradient(90deg,#1f9e68,#4cc28d);height:20px;top:38px}
.pic.blue-glasses{background:linear-gradient(90deg,#cde1f3,#6fa4d6);height:28px;top:32px;border-radius:6px}
.card .name{position:absolute;left:0;width:100%;top:97px;font-size:8px;color:var(--text)}
.card.featured .name{color:var(--green)}
.card .rule{position:absolute;left:18px;right:18px;top:111px;height:1px;background:var(--line)}
.card .price{position:absolute;left:0;width:100%;top:118px;font-size:14px;color:var(--green)}
.btn{position:absolute;top:117px;height:21px;font-size:7.5px;color:var(--white);font-weight:700;padding-top:6px}
.btn.detail{left:13px;width:62px;background:var(--green)}
.btn.cart{left:81px;width:63px;background:var(--ink)}

.whats-new{left:258px;top:380px;width:148px;height:216px;text-align:center}
.whats-new h4{position:absolute;top:23px;width:100%;font-weight:400;font-size:9.5px;color:var(--text)}
.whats-new .figure{position:absolute;left:37px;top:41px;width:66px;height:93px;background:linear-gradient(180deg,#f0d9b8,#3f8a3a 70%,#e9e9e9);border-radius:4px}
.whats-new p{position:absolute;top:145px;left:10px;right:10px;font-size:7px;line-height:11px;color:var(--text)}
.whats-new .view{position:absolute;top:190px;width:100%;font-size:6.5px;color:var(--ink);text-decoration:underline}

.stars{display:flex;gap:1px}
.stars i{width:9px;height:9px;background:var(--green);clip-path:polygon(50% 0,61% 35%,98% 35%,68% 57%,79% 91%,50% 70%,21% 91%,32% 57%,2% 35%,39% 35%)}
.stars i.off{background:#bbb}

.latest-rule{left:434px;top:609px;width:499px;height:1px;background:var(--line)}
.latest-title{left:434px;top:620px;font-size:10.5px;color:var(--ink)}
.thumb{top:656px;width:85px;height:90px;border:1px solid #ddd;background:var(--white)}
.thumb.active{border-color:var(--green)}
.thumb .photo{position:absolute;inset:3px;background:linear-gradient(180deg,#f1e1cb 0%,#d9b98f 35%,#3c7d34 70%,#f4f4f4 100%)}
.thumb .photo.alt{background:linear-gradient(180deg,#f2e3c8 0%,#e4c78f 35%,#2d2d2d 70%,#f4f4f4 100%)}
.thumb .photo.brown{background:linear-gradient(180deg,#f1e1cb 0%,#c9863c 45%,#a46a2b 80%,#f4f4f4 100%)}
.thumb-name{font-size:7.5px;color:var(--text)}
.thumb-name.active{color:var(--green)}
.thumb-price{font-size:7px}
.thumb-price s{color:#777;margin-right:5px}
.thumb-price b{color:var(--red);font-weight:400}

/* partners */
.partners{left:258px;top:824px;width:704px;height:55px;background:var(--white)}
.partner{position:absolute;top:19px;font-size:11px;font-weight:700;color:var(--ink);display:flex;align-items:center;gap:5px}
.partner i{display:block;width:9px;height:9px;background:#9a9a9a}
.partner-sep{position:absolute;top:18px;width:1px;height:22px;background:var(--line)}

/* footer */
.f-head{top:900px;font-size:9.5px;color:var(--ink)}
.f-rule{top:921px;height:1px;background:#d6d6d6}
.f-links{top:933px;font-size:7.5px;line-height:10.8px;color:var(--text)}
.blog-item{left:533px;width:118px;font-size:7px;color:var(--text);padding-bottom:5px;border-bottom:1px solid #d6d6d6}
.blog-item.last{border-bottom:0}
.newsletter{left:703px;top:934px;width:92px;height:25px;border:1px solid #d6d6d6;background:var(--white);font-size:7px;color:#aaa;padding:8px 0 0 6px}
.news-go{left:795px;top:934px;width:21px;height:25px;background:var(--green);color:var(--ink);font-size:7.5px;text-align:center;padding-top:8px}
.social{top:931px;width:16px;height:16px;border-radius:50%;background:#b3b3b3}
.bottom-rule{left:258px;top:1016px;width:704px;height:1px;background:#d6d6d6}
.copyright{left:258px;top:1031px;font-size:7px;color:var(--text)}
.pay{top:1028px;height:23px;width:33px;border:1px solid #d0d0d0;background:var(--white);font-size:7px;font-weight:700;color:var(--ink);text-align:center;padding-top:7px}
</style>
</head>
<body>
<div class="canvas">
  <div class="abs topbar"></div>
  <div class="abs backdrop" role="img" aria-label="Soft blurred festival photograph behind the shop"></div>
  <div class="abs ground"></div>
  <div class="abs shell"></div>

  <!-- top bar -->
  <div class="abs welcome">WELCOME VISITOR YOU CAN <b>LOGIN</b> OR <em>CREATE AN ACCOUNT</em></div>
  <div class="abs currency" style="left:710px">EUR €</div>
  <div class="abs currency" style="left:758px">GBP €</div>
  <div class="abs account-links">My Account<span>|</span>Shopping Cart<span>|</span>Checkout</div>

  <!-- header -->
  <div class="abs brand"><i></i>Feestkraamwinkel</div>
  <div class="abs search">
    <div class="cat">All Categories</div>
    <div class="field">Search Entire Store here</div>
    <div class="go">
      <svg width="25" height="25" viewBox="0 0 25 25"><circle cx="11" cy="11" r="4" fill="none" stroke="#fff" stroke-width="1.6"/><line x1="14" y1="14" x2="17.5" y2="17.5" stroke="#fff" stroke-width="2"/></svg>
    </div>
  </div>
  <div class="abs mini-cart">
    <svg class="abs" style="left:12px;top:6px" width="16" height="13" viewBox="0 0 16 13"><path d="M0 1h3l2 7h8l2-5H4" fill="none" stroke="#444" stroke-width="1.3"/><circle cx="6" cy="11" r="1.3" fill="#444"/><circle cx="12" cy="11" r="1.3" fill="#444"/></svg>
    <span class="count">0 ITEM(S) - $0.00</span>
    <span class="drop"></span>
  </div>

  <!-- navigation -->
  <div class="abs nav-products">PRODUCTS LIST</div>
  <nav class="abs nav-main">
    <a style="margin-left:42px">HOME</a>
    <a style="margin-left:43px">INFORMATIE</a>
    <a style="margin-left:49px">LINKS</a>
    <a style="margin-left:41px">CONTACT</a>
  </nav>
  <div class="abs nav-cart">
    <svg class="abs" style="left:14px;top:9px" width="14" height="12" viewBox="0 0 16 13"><path d="M0 1h3l2 7h8l2-5H4" fill="none" stroke="#fff" stroke-width="1.5"/><circle cx="6" cy="11" r="1.3" fill="#fff"/><circle cx="12" cy="11" r="1.3" fill="#fff"/></svg>
    Winkelwagen
  </div>

  <!-- content panel -->
  <div class="abs content"></div>

  <div class="abs side-box cat-list">
    <div class="cat-item" style="top:7px">Lorem Ipsum</div>
    <div class="cat-item" style="top:29px">Lorem</div>
    <div class="cat-item" style="top:50px">Lorem Ipsum</div>
    <div class="cat-item" style="top:71px">Lorem Ipsum Lorem</div>
    <div class="cat-item" style="top:92px">Lorem Ipsum</div>
    <div class="cat-item" style="top:113px">Lorem</div>
    <div class="cat-item active" style="top:134px">Clothing Accessories</div>
    <div class="cat-item last" style="top:155px">Lorem Ipsum</div>
  </div>

  <div class="abs flyout">
    <h3>Clothing Accessories</h3>
    <div class="rule"></div>
    <a class="current" style="top:63px">Glasses</a>
    <a style="top:85px">Tiroler Stocking</a>
    <a style="top:108px">Other Accessories</a>
    <a style="top:130px">Wings</a>
  </div>

  <div class="abs top-rule"></div>

  <!-- product grid -->
  <div class="abs card featured" style="left:609px;top:226px">
    <div class="pic bavarian" role="img" aria-label="Bavarian party glasses with blue and white pattern"></div>
    <div class="name">Bril Bavarian Oktoberfest</div>
    <div class="btn detail">☰ View Detail</div>
    <div class="btn cart">Add to Cart</div>
  </div>
  <div class="abs card" style="left:777px;top:226px">
    <div class="pic green-glasses" role="img" aria-label="Green beer-glass party spectacles"></div>
    <div class="name">Bril bierglazen groen</div>
    <div class="rule"></div>
    <div class="price">$100.00</div>
  </div>
  <div class="abs card" style="left:437px;top:385px">
    <div class="pic green-glasses" role="img" aria-label="Green beer-glass party spectacles"></div>
    <div class="name">Bril bierglazen groen</div>
    <div class="rule"></div>
    <div class="price">$100.00</div>
  </div>
  <div class="abs card" style="left:609px;top:385px">
    <div class="pic blue-glasses" role="img" aria-label="White glasses with blue checked arms"></div>
    <div class="name">Party Shades glasses Oktoberfest</div>
    <div class="rule"></div>
    <div class="price">$100.00</div>
  </div>
  <div class="abs card" style="left:777px;top:385px">
    <div class="pic blue-glasses" role="img" aria-label="White glasses with blue checked arms"></div>
    <div class="name">Party Shades glasses Oktoberfest</div>
    <div class="rule"></div>
    <div class="price">$100.00</div>
  </div>

  <!-- what's new -->
  <div class="abs side-box whats-new">
    <h4>What's New?</h4>
    <div class="figure" role="img" aria-label="Model in a green dirndl holding a beer"></div>
    <p>Lorem Ipsum is simply dummy text of the printing and typesetting</p>
    <div class="stars abs" style="left:51px;top:173px"><i></i><i></i><i></i><i class="off"></i><i class="off"></i></div>
    <div class="view">VIEW ALL</div>
  </div>

  <!-- latest products -->
  <div class="abs latest-rule"></div>
  <div class="abs latest-title">Latest &nbsp;Products</div>

  <div class="abs thumb" style="left:434px"><div class="photo alt" role="img" aria-label="Woman in black dirndl with braids"></div></div>
  <div class="abs thumb" style="left:536px"><div class="photo" role="img" aria-label="Woman in green dirndl holding a beer"></div></div>
  <div class="abs thumb active" style="left:642px"><div class="photo brown" role="img" aria-label="Woman in brown dirndl"></div></div>
  <div class="abs thumb" style="left:747px"><div class="photo alt" role="img" aria-label="Woman in black dirndl with braids"></div></div>
  <div class="abs thumb" style="left:849px"><div class="photo" role="img" aria-label="Woman in green dirndl holding a beer"></div></div>

  <div class="abs thumb-name" style="left:434px;top:755px">Lorem Ipsum Name</div>
  <div class="abs thumb-name" style="left:536px;top:755px">Lorem Ipsum Name</div>
  <div class="abs thumb-name active" style="left:642px;top:755px">Lorem Ipsum Name</div>
  <div class="abs thumb-name" style="left:747px;top:755px">Lorem Ipsum Name</div>
  <div class="abs thumb-name" style="left:849px;top:755px">Lorem Ipsum Name</div>

  <div class="abs thumb-price" style="left:434px;top:768px"><s>$ 12.00</s><b>$ 09.00</b></div>
  <div class="abs thumb-price" style="left:536px;top:768px"><s>$ 12.00</s><b>$ 09.00</b></div>
  <div class="abs thumb-price" style="left:642px;top:768px"><s>$ 12.00</s><b>$ 09.00</b></div>
  <div class="abs thumb-price" style="left:747px;top:768px"><s>$ 12.00</s><b>$ 09.00</b></div>
  <div class="abs thumb-price" style="left:849px;top:768px"><s>$ 12.00</s><b>$ 09.00</b></div>

  <div class="abs stars" style="left:434px;top:780px"><i></i><i></i><i></i><i class="off"></i><i class="off"></i></div>
  <div class="abs stars" style="left:536px;top:780px"><i></i><i></i><i></i><i class="off"></i><i class="off"></i></div>
  <div class="abs stars" style="left:642px;top:780px"><i></i><i></i><i></i><i class="off"></i><i class="off"></i></div>
  <div class="abs stars" style="left:747px;top:780px"><i></i><i></i><i></i><i class="off"></i><i class="off"></i></div>
  <div class="abs stars" style="left:849px;top:780px"><i></i><i></i><i></i><i class="off"></i><i class="off"></i></div>

  <!-- partners -->
  <div class="abs partners">
    <div class="partner" style="left:44px"><i></i>Grapwinkel</div>
    <div class="partner-sep" style="left:144px"></div>
    <div class="partner" style="left:184px"><i></i>ParcelLine</div>
    <div class="partner-sep" style="left:291px"></div>
    <div class="partner" style="left:305px"><i></i>PayDirect</div>
    <div class="partner-sep" style="left:389px"></div>
    <div class="partner" style="left:405px"><i></i>WalletPay</div>
  </div>

  <!-- footer -->
  <div class="abs f-head" style="left:258px">Site Info</div>
  <div class="abs f-rule" style="left:258px;width:224px"></div>
  <div class="abs f-links" style="left:258px">Shipping and Return<br>Right of Withdraw<br>Imprint<br>Privacy Notice<br>Contact Us</div>
  <div class="abs f-links" style="left:400px">Create New Account<br>Login<br>Track your order<br>Shopping Cart</div>

  <div class="abs f-head" style="left:533px">Latest Blog Post</div>
  <div class="abs f-rule" style="left:533px;width:93px"></div>
  <div class="abs blog-item" style="top:943px">Lorem Ipsum is simply dummy text</div>
  <div class="abs blog-item" style="top:964px">Lorem Ipsum is simply dummy text</div>
  <div class="abs blog-item last" style="top:983px">Lorem Ipsum is simply dummy text</div>

  <div class="abs f-head" style="left:703px">Newsletter</div>
  <div class="abs f-rule" style="left:703px;width:112px"></div>
  <div class="abs newsletter">email@example.com</div>
  <div class="abs news-go">GO</div>

  <div class="abs f-head" style="left:866px">Social Link</div>
  <div class="abs f-rule" style="left:866px;width:96px"></div>
  <div class="abs social" style="left:866px"></div>
  <div class="abs social" style="left:889px"></div>
  <div class="abs social" style="left:912px"></div>
  <div class="abs social" style="left:935px"></div>

  <div class="abs bottom-rule"></div>
  <div class="abs copyright">Copyright © 2014 Company Name</div>
  <div class="abs pay" style="left:856px">Wallet</div>
  <div class="abs pay" style="left:893px">CardOne</div>
  <div class="abs pay" style="left:930px">Cardix</div>
</div>
</body>
</html>
```